Builder of high-end, expensive tables and other furniture

Build a website that represents what we do. I want a luxury feel that appeals to those who can afford our products. We build very high end tables and other furniture using trees that have fallen or are standing dead. We never cut living trees. Trees are harvested, milled, and kiln dried. Then that lumber is meticulously turned into fine furniture using the best equipment. Our furniture prices range from $1,000-$20,000.

Trying to figure out how to raise my spend.

```html
<!DOCTYPE html>
<html lang="en">
<head>
<meta charset="utf-8">
<title>Heartwood Tables — Fine Furniture from Fallen Trees</title>
<link href="https://fonts.googleapis.com/css2?family=Poppins:wght@400;500;600;700;800&display=swap" rel="stylesheet">
<style>
  :root {
    --navy: #062c43;
    --orange: #e8643a;
    --frame-red: #e8321f;
    --ink: #111111;
    --text: #2b2b2b;
    --blush: #fcefea;
    --footer-bg: #ebf1f8;
    --white: #ffffff;
  }
  * { box-sizing: border-box; margin: 0; padding: 0; }
  html, body { width: 1200px; height: 3311px; overflow: hidden; }
  body { position: relative; background: var(--white); font-family: "Poppins", sans-serif; color: var(--text); }
  .abs { position: absolute; }
  a { color: inherit; text-decoration: none; }

  /* Header & hero */
  .hero-band { left: 0; top: 0; width: 1200px; height: 600px; }
  .brand { display: flex; align-items: center; gap: 8px; font-weight: 500; color: var(--orange); font-size: 28px; letter-spacing: -0.3px; }
  .brand-dot { width: 16px; height: 16px; border-radius: 50%; background: var(--orange); flex: none; }
  .site-brand { left: 15px; top: 20px; }
  .main-nav { left: 424px; top: 30px; display: flex; gap: 25px; font-size: 16px; color: var(--white); font-weight: 500; }
  .main-nav .is-active { color: var(--orange); font-weight: 600; border-bottom: 2px solid var(--orange); line-height: 20px; }
  .search { left: 871px; top: 30px; color: var(--white); font-size: 16px; font-weight: 500; display: flex; align-items: center; gap: 6px; }
  .account-btn { left: 964px; top: 23px; width: 121px; height: 36px; border-radius: 18px; background: var(--white); color: var(--ink); font-size: 15px; display: flex; align-items: center; justify-content: center; }
  .hero-frame { left: 220px; top: 116px; width: 503px; height: 415px; border: 7px solid var(--frame-red); }
  .hero-photo { left: 0; top: 123px; width: 711px; height: 400px; background: linear-gradient(135deg, #3a1d12 0%, #6b3a22 45%, #2a140b 100%); }
  .hero-title { left: 731px; top: 178px; color: var(--white); font-weight: 800; font-size: 47px; line-height: 68px; letter-spacing: 0.5px; }
  .btn { display: flex; align-items: center; justify-content: center; background: var(--orange); color: var(--white); font-weight: 700; font-size: 15px; width: 189px; height: 54px; }
  .hero-btn { left: 732px; top: 324px; }

  /* Popular products */
  .section-title { left: 0; width: 1200px; text-align: center; color: var(--ink); font-weight: 700; }
  .products-title { top: 676px; font-size: 33px; }
  .products-intro { left: 250px; top: 728px; width: 700px; text-align: center; font-size: 15px; line-height: 30px; color: var(--text); }
  .product { top: 851px; width: 314px; text-align: center; }
  .product-photo { height: 213px; }
  .product-name { margin-top: 28px; font-weight: 600; font-size: 18px; color: var(--ink); }
  .product-price { margin-top: 6px; font-size: 19px; color: var(--ink); }

  /* About */
  .about-photo { left: 0; top: 1200px; width: 600px; height: 418px; background: linear-gradient(135deg, #e9e2d6 0%, #cfae86 50%, #f1ede7 100%); }
  .about-panel { left: 600px; top: 1200px; width: 600px; height: 418px; background: var(--blush); }
  .about-title { left: 600px; top: 1260px; width: 485px; text-align: center; color: var(--ink); font-weight: 700; font-size: 42px; }
  .about-text { left: 616px; top: 1336px; width: 457px; text-align: justify; text-align-last: center; font-size: 17.5px; line-height: 31px; color: var(--text); }
  .about-btn { left: 732px; top: 1429px; }

  /* Process */
  .process-title { top: 1730px; font-size: 42px; }
  .step-photo { width: 454px; height: 299px; }
  .step-heading { font-weight: 600; font-size: 20px; color: var(--ink); }
  .step-text { width: 444px; font-size: 21.5px; line-height: 37px; text-align: justify; color: var(--text); }

  /* Footer */
  .site-footer { left: 0; top: 2945px; width: 1200px; height: 366px; background: var(--footer-bg); }
  .footer-brand { left: 116px; top: 3010px; }
  .social { top: 3081px; width: 24px; height: 24px; border-radius: 50%; background: var(--ink); }
  .footer-heading { top: 3024px; font-weight: 600; font-size: 18px; color: var(--ink); }
  .footer-links { left: 491px; top: 3086px; list-style: none; font-size: 18px; line-height: 34.5px; color: var(--ink); }
  .footer-services { left: 815px; top: 3086px; width: 280px; font-size: 18px; line-height: 34.5px; color: var(--ink); }
  .copyright { left: 0; top: 3252px; width: 1200px; text-align: center; font-size: 17px; color: var(--ink); }
</style>
</head>
<body>

<header>
  <svg class="abs hero-band" width="1200" height="600" viewBox="0 0 1200 600" aria-hidden="true">
    <polygon points="407,0 1200,0 1200,600 561,600" fill="var(--navy)"/>
  </svg>
  <div class="abs brand site-brand"><span class="brand-dot"></span>Heartwood Tables</div>
  <nav class="abs main-nav">
    <a class="is-active" href="#">Home</a>
    <a href="#">About Us</a>
    <a href="#">Product</a>
    <a href="#">Blog</a>
    <a href="#">Contact Us</a>
  </nav>
  <div class="abs search">Search
    <svg width="16" height="16" viewBox="0 0 16 16" aria-hidden="true"><circle cx="7" cy="7" r="5" fill="none" stroke="#fff" stroke-width="1.5"/><line x1="11" y1="11" x2="15" y2="15" stroke="#fff" stroke-width="1.5"/></svg>
  </div>
  <a class="abs account-btn" href="#">My Account</a>
</header>

<section class="hero">
  <div class="abs hero-frame"></div>
  <div class="abs hero-photo" role="img" aria-label="Wood-panelled study with a carved desk and leather chairs"></div>
  <h1 class="abs hero-title">WELCOME<br>HEARTWOOD TABLES</h1>
  <a class="abs btn hero-btn" href="#">SHOP NOW</a>
</section>

<section class="products">
  <h2 class="abs section-title products-title">POPULAR PRODUCTS</h2>
  <p class="abs products-intro">Lorem ipsum dolor sit amet, consectetur adipiscing elit, sed do eiusmod tempor incididunt ut labore et dolore magna aliqua. Ut enim ad minim veniam, quis nostrud exercitation ullamco laboris nisi ut aliquip ex ea commodo consequat. Duis aute</p>
  <div class="abs product" style="left:112px">
    <div class="product-photo" role="img" aria-label="Navy tufted armchair in a bright room" style="background:linear-gradient(135deg,#f2f2f0 0%,#d9dadb 55%,#2a3560 100%)"></div>
    <div class="product-name">SOFA</div>
    <div class="product-price">$ 1500</div>
  </div>
  <div class="abs product" style="left:442px">
    <div class="product-photo" role="img" aria-label="Wooden outdoor lounge and coffee table on a deck" style="background:linear-gradient(180deg,#dfe8ef 0%,#8fa06a 45%,#b88d5e 100%)"></div>
    <div class="product-name">TABLE</div>
    <div class="product-price">$ 18000</div>
  </div>
  <div class="abs product" style="left:774px">
    <div class="product-photo" role="img" aria-label="Light wood dining table with chairs" style="background:linear-gradient(180deg,#eeece8 0%,#e3dcd1 60%,#cdb08a 100%)"></div>
    <div class="product-name">CHAIR</div>
    <div class="product-price">$ 1900</div>
  </div>
</section>

<section class="about">
  <div class="abs about-photo" role="img" aria-label="Modern kitchen with wood and white cabinets"></div>
  <div class="abs about-panel"></div>
  <h2 class="abs about-title">ABOUT US</h2>
  <p class="abs about-text">We build very high end tables and other furniture using trees that have fallen or are standing dead.</p>
  <a class="abs btn about-btn" href="#">SHOP NOW</a>
</section>

<section class="process">
  <h2 class="abs section-title process-title">HOW IT WORK</h2>

  <div class="abs step-photo" role="img" aria-label="Fallen tree resting in a green yard" style="left:127px;top:1832px;border-radius:0 0 40px 0;background:linear-gradient(135deg,#7a6a52 0%,#6f9a4a 50%,#c9dcb4 100%)"></div>
  <h3 class="abs step-heading" style="left:617px;top:1830px">HARVESTED</h3>
  <p class="abs step-text" style="left:630px;top:1862px">Lorem ipsum dolor sit amet, consectetur adipiscing elit, sed do eiusmod tempor incididunt ut labore et dolore magna aliqua. Ut enim ad minim veniam, quis nostrud exercitation ullamco laboris nisi ut aliquip ex ea commodo consequat.</p>

  <h3 class="abs step-heading" style="left:117px;top:2199px">MILLED</h3>
  <p class="abs step-text" style="left:130px;top:2231px">Lorem ipsum dolor sit amet, consectetur adipiscing elit, sed do eiusmod tempor incididunt ut labore et dolore magna aliqua. Ut enim ad minim veniam, quis nostrud exercitation ullamco laboris nisi ut aliquip ex ea commodo consequat.</p>
  <div class="abs step-photo" role="img" aria-label="Logs stacked in a dusty sawmill yard" style="left:614px;top:2201px;border-radius:40px 0 40px 0;background:linear-gradient(135deg,#3b2a22 0%,#8a5a3a 55%,#b3774a 100%)"></div>

  <div class="abs step-photo" role="img" aria-label="Stack of kiln dried lumber boards" style="left:127px;top:2578px;border-radius:0 0 40px 0;background:linear-gradient(135deg,#8f8f8a 0%,#d6b48c 45%,#e8d2b2 100%)"></div>
  <h3 class="abs step-heading" style="left:622px;top:2577px">KILN DRIED</h3>
  <p class="abs step-text" style="left:630px;top:2609px">Lorem ipsum dolor sit amet, consectetur adipiscing elit, sed do eiusmod tempor incididunt ut labore et dolore magna aliqua. Ut enim ad minim veniam, quis nostrud exercitation ullamco laboris nisi ut aliquip ex ea commodo consequat.</p>
</section>

<footer>
  <div class="abs site-footer"></div>
  <div class="abs brand footer-brand"><span class="brand-dot"></span>Heartwood Tables</div>
  <a class="abs social" href="#" aria-label="Social profile" style="left:162px"></a>
  <a class="abs social" href="#" aria-label="Social profile" style="left:214px"></a>
  <a class="abs social" href="#" aria-label="Social profile" style="left:267px"></a>

  <h4 class="abs footer-heading" style="left:491px">QUICK LINKS</h4>
  <ul class="abs footer-links">
    <li><a href="#">Home</a></li>
    <li><a href="#">About Us</a></li>
    <li><a href="#">Services</a></li>
    <li><a href="#">Contact Us</a></li>
  </ul>

  <h4 class="abs footer-heading" style="left:815px">SERVICES</h4>
  <p class="abs footer-services">Lorem ipsum dolor sit amet, consectetur adipiscing elit, sed do eiusmod tempor incididunt ut labore et</p>

  <p class="abs copyright">CopyRight@2023Heartwood Tables | Al Right Reserved</p>
</footer>

</body>
</html>
```